Experienced and Professional Marriage Celebrant

I need a web design for my services as a marriage celebrant in the Sydney area. I want people to have the impression I am a modern and professional marriage celebrant who can tailor a wedding ceremony and execute the ceremony with a high level of care and accommodate and adapt to any style of wedding and personalities of couples. I like a mint and pink and black theme and I am not sure whether to use the professional photos of me, might be too stiff! But would like to see ideas you can come up with. Happy to use other photos you might have
Updates

Project Deadline Extended
Reason: I have haven't been able to respond as quickly as I would have liked this last week to comments so extending a few days. Thanks

Industry/Entity Type

It Professional

```html
<!DOCTYPE html>
<html lang="en">
<head>
<meta charset="utf-8">
<title>Lena Hartley Celebrant — Gallery</title>
<link href="https://fonts.googleapis.com/css2?family=Roboto:wght@300;400;500&display=swap" rel="stylesheet">
<style>
:root{
  --black:#000;
  --nav:#3d3d3d;
  --nav-edge:#5a5a5a;
  --pink:#f46fbf;
  --lime:#a3db45;
  --white:#fff;
  --heading:#333;
  --body:#555;
  --footer:#333;
  --footer-text:#d6d6d6;
}
*{box-sizing:border-box;margin:0;padding:0}
html,body{width:1041px;height:1200px;overflow:hidden;background:var(--white);font-family:"Roboto",Arial,sans-serif}
.site-header{height:63px;background:var(--black);display:flex;align-items:center;justify-content:space-between;padding:0 64px}
.brand{color:var(--white);font-size:24px;font-weight:500;letter-spacing:1.2px}
.header-contact{display:flex;align-items:center;gap:6px;color:var(--lime);font-size:14px;letter-spacing:.3px}
.header-contact .number{color:var(--white)}
.header-contact svg{margin-right:4px}
.social-dots{display:flex;gap:4px;margin-left:14px}
.social-dots span{width:17px;height:17px;border-radius:50%;background:var(--pink)}
.main-nav{height:38px;background:var(--nav);border-bottom:2px solid var(--nav-edge);display:flex;padding-left:64px}
.main-nav a{color:var(--white);text-decoration:none;font-size:12px;letter-spacing:.3px;display:flex;align-items:center;padding:0 16px;height:38px}
.main-nav a:nth-child(n+2){margin-left:20px}
.main-nav a.active{background:var(--lime);color:#222}
.hero{height:174px;background:linear-gradient(90deg,#c98c5a 0%,#e9c9a8 22%,#efe6dc 45%,#d9d4cf 65%,#c8b8aa 80%,#b9b3ad 100%)}
.gallery{padding:35px 64px 0}
.gallery-title{font-size:20px;font-weight:400;color:#111;letter-spacing:.5px;margin-bottom:18px}
.gallery-title em{font-style:normal;color:var(--pink)}
.gallery-grid{display:grid;grid-template-columns:repeat(3,258px);column-gap:69px;grid-template-rows:239px 253px auto}
.photo{height:145px}
.card h3{font-size:13px;font-weight:500;color:var(--heading);margin:16px 0 4px;letter-spacing:.3px}
.card p{font-size:11.5px;font-weight:300;color:var(--body);line-height:18.5px;letter-spacing:.2px}
.row-2 h3{margin-top:22px}
.site-footer{position:absolute;left:0;top:1110px;width:1041px;height:90px;background:var(--footer);display:flex;align-items:center;justify-content:space-between;padding:0 64px}
.copyright{color:var(--footer-text);font-size:9.5px;line-height:12px;font-weight:300;letter-spacing:.2px}
.connect{display:flex;align-items:center;gap:6px;color:var(--white);font-size:9px;letter-spacing:.4px}
.connect .dot{width:26px;height:26px;border-radius:50%}
.connect .dot:nth-of-type(1){margin-left:8px;background:#3b5ea0}
.connect .dot:nth-of-type(2){background:#29a9df}
.connect .dot:nth-of-type(3){background:#d62420}
</style>
</head>
<body>
<header class="site-header">
  <div class="brand">LENA HARTLEY CELEBRANT</div>
  <div class="header-contact">
    <svg width="13" height="13" viewBox="0 0 13 13" aria-hidden="true"><rect width="13" height="13" rx="2" fill="#a3db45"/><path d="M4 3c1 0 1.3 1.5 1 2l-.6.5c.5 1.2 1.3 2 2.5 2.6l.6-.6c.5-.3 2 0 2 1s-1 1.5-2 1.2C5.3 9.1 3.6 7.4 3 5 2.7 4 3 3 4 3z" fill="#000"/></svg>
    <span>CALL US:</span><span class="number">123-456-7890</span>
    <div class="social-dots"><span></span><span></span><span></span></div>
  </div>
</header>
<nav class="main-nav">
  <a href="#">HOME</a><a href="#">ABOUT US</a><a href="#">SERVICES</a><a href="#">NEWS &amp; EVENTS</a><a href="#" class="active">GALLERY</a><a href="#">TESTIMONIALS</a><a href="#">BLOG</a><a href="#">CONTACT US</a>
</nav>
<div class="hero" role="img" aria-label="Gold wedding rings with bells and pink flowers beside a smiling bride and groom"></div>
<main class="gallery">
  <h1 class="gallery-title">PHOTO <em>GALLERY</em></h1>
  <div class="gallery-grid">
    <div class="card"><div class="photo" role="img" aria-label="Seaside timber deck with tables and umbrellas" style="background:linear-gradient(180deg,#8fb4d6 0%,#3f78a8 35%,#8a7a68 60%,#5b4b3d 100%)"></div><h3>Heading 1</h3><p>Aliquam molestie, mi et imperdiet euismod, dui purus auctor tellus, et interdum lacus</p></div>
    <div class="card"><div class="photo" role="img" aria-label="Decorated reception hall with floral table settings" style="background:linear-gradient(160deg,#8a3a2e 0%,#c86a9a 40%,#e8b070 65%,#c2302e 100%)"></div><h3>Heading 1</h3><p>Aliquam molestie, mi et imperdiet euismod, dui purus auctor tellus, et interdum lacus</p></div>
    <div class="card"><div class="photo" role="img" aria-label="Couple embracing by the water at sunset" style="background:linear-gradient(180deg,#6b5330 0%,#3e3020 45%,#5a5550 70%,#2a221c 100%)"></div><h3>Heading 1</h3><p>Aliquam molestie, mi et imperdiet euismod, dui purus auctor tellus, et interdum lacus</p></div>
    <div class="card row-2"><div class="photo" role="img" aria-label="Garden venue with gazebo and white chairs before a large house" style="background:linear-gradient(180deg,#b9c7d6 0%,#9a8f80 40%,#e7e7e4 70%,#4d7a2e 100%)"></div><h3>Heading 1</h3><p>Aliquam molestie, mi et imperdiet euismod, dui purus auctor tellus, et interdum lacus</p></div>
    <div class="card row-2"><div class="photo" role="img" aria-label="Wedding party walking along a sandy beach" style="background:linear-gradient(180deg,#7fa6c4 0%,#a9bcc6 35%,#5f6a4a 50%,#b48f68 75%,#a0784f 100%)"></div><h3>Heading 1</h3><p>Aliquam molestie, mi et imperdiet euismod, dui purus auctor tellus, et interdum lacus</p></div>
    <div class="card row-2"><div class="photo" role="img" aria-label="Draped reception room with candlelit tables" style="background:linear-gradient(180deg,#c8a8b4 0%,#b08a8a 40%,#3a2a26 70%,#1e1614 100%)"></div><h3>Heading 1</h3><p>Aliquam molestie, mi et imperdiet euismod, dui purus auctor tellus, et interdum lacus</p></div>
    <div class="card"><div class="photo" role="img" aria-label="Couple embracing by the water at sunset" style="background:linear-gradient(180deg,#6b5330 0%,#3e3020 45%,#5a5550 70%,#2a221c 100%)"></div><h3>Heading 1</h3><p>Aliquam molestie, mi et imperdiet euismod, dui purus auctor tellus, et interdum lacus</p></div>
    <div class="card"><div class="photo" role="img" aria-label="Bride, groom and family group outdoors" style="background:linear-gradient(180deg,#7b7468 0%,#a8a39a 40%,#c7b8ad 65%,#6b8a46 100%)"></div><h3>Heading 1</h3><p>Aliquam molestie, mi et imperdiet euismod, dui purus auctor tellus, et interdum lacus</p></div>
    <div class="card"><div class="photo" role="img" aria-label="Close view of the couple's hands with wedding rings" style="background:linear-gradient(135deg,#c9b8a4 0%,#8a6a50 45%,#3a2a20 70%,#b8a690 100%)"></div><h3>Heading 1</h3><p>Aliquam molestie, mi et imperdiet euismod, dui purus auctor tellus, et interdum lacus</p></div>
  </div>
</main>
<footer class="site-footer">
  <p class="copyright">Copyright © 2014. Lena Hartley Celebrant.<br>All Right Reserved</p>
  <div class="connect">CONNECT US:<span class="dot"></span><span class="dot"></span><span class="dot"></span></div>
</footer>
</body>
</html>
```